Home Staging Company needs business card design

We're a home staging company called Brightly Settled Home Staging. We would like a business card design that includes aqua and gray. Our current logo of house within chair is fine but I find we almost always use the logo in one color. I'll upload images of front and back of our current card and our logo. Note that we have dropped "Solutions" from our company name and don't want to include it on the card.

Target Market(s)

Realtors and homeowners - people interested in selling their homes

Contact Information for Business Card

Marisol Thistlewood
Brightly Settled Home Staging
757-555-0193
www.brightlysettled.com
marisol@brightlysettled.com

Font styles to use
Serif
Script

Requirements
Must have
• My logo and contact details
• UPDATE***
• I forgot to say that the company name should be included on the front of the card somehow.

```html
<!DOCTYPE html>
<html lang="en">
<head>
<meta charset="utf-8">
<title>Brightly Settled Home Staging – Business Card</title>
<link href="https://fonts.googleapis.com/css2?family=Questrial&display=swap" rel="stylesheet">
<style>
  :root {
    --backdrop: #4a4a4a;
    --card: #262626;
    --card-edge: #1c1c1c;
    --mark-tone: #3d3d3d;
    --aqua: #4fb9c5;
    --white: #f2f2f2;
    --muted: #bdbdbd;
  }
  * { margin: 0; padding: 0; box-sizing: border-box; }
  html, body {
    width: 799px; height: 1200px; overflow: hidden;
    background: var(--backdrop);
    font-family: "Questrial", sans-serif;
  }
  .sheet {
    position: relative; width: 799px; height: 1200px;
    display: flex; flex-direction: column; align-items: center; justify-content: center; gap: 110px;
  }
  .card {
    position: relative; width: 660px; height: 377px;
    background: var(--card);
    box-shadow: 0 18px 40px rgba(0,0,0,.45);
    overflow: hidden;
  }
  /* Front */
  .front-brand {
    position: absolute; inset: 0;
    display: flex; flex-direction: column; align-items: center; justify-content: center; gap: 22px;
  }
  .front-dot {
    width: 120px; height: 120px; border-radius: 50%;
    background: var(--mark-tone);
  }
  .front-name {
    color: var(--mark-tone);
    font-size: 30px; letter-spacing: 1px;
  }
  /* Back */
  .back-brand {
    position: absolute; left: 48px; top: 118px; width: 250px;
    display: flex; flex-direction: column; align-items: center; gap: 18px;
  }
  .back-dot {
    width: 84px; height: 84px; border-radius: 50%;
    background: var(--aqua);
  }
  .back-name {
    color: var(--white); font-size: 24px; line-height: 1.25; text-align: center;
  }
  .person {
    position: absolute; left: 360px; top: 130px;
  }
  .person-name { font-size: 26px; color: var(--white); }
  .person-name .surname { color: var(--aqua); }
  .person-title { font-size: 14px; color: var(--muted); margin-top: 4px; }
  .contact-list { list-style: none; margin-top: 16px; }
  .contact-list li {
    display: flex; align-items: center; gap: 12px;
    font-size: 16px; color: var(--white); line-height: 27px;
  }
  .contact-list svg { width: 14px; height: 14px; flex: none; }
  .accent-rule {
    position: absolute; left: 0; right: 0; bottom: 22px; height: 5px;
    background: var(--aqua);
  }
  .base-strip {
    position: absolute; left: 0; right: 0; bottom: 0; height: 22px;
    background: var(--card-edge);
  }
</style>
</head>
<body>
  <main class="sheet">
    <section class="card card-front" aria-label="Card front">
      <div class="front-brand">
        <div class="front-dot"></div>
        <div class="front-name">Brightly Settled Home Staging</div>
      </div>
    </section>

    <section class="card card-back" aria-label="Card back">
      <div class="back-brand">
        <div class="back-dot"></div>
        <div class="back-name">Brightly Settled<br>Home Staging</div>
      </div>

      <div class="person">
        <div class="person-name">Marisol <span class="surname">Thistlewood</span></div>
        <div class="person-title">Managing Director</div>
        <ul class="contact-list">
          <li>
            <svg viewBox="0 0 16 16" aria-hidden="true"><path fill="#4fb9c5" d="M3.6 1.5l2.3 2.6-1.3 1.8c.9 2 2.5 3.6 4.5 4.5l1.8-1.3 2.6 2.3-1.3 2.1C7 13.2 2.8 9 1.5 2.8z"/></svg>
            757-555-0193
          </li>
          <li>
            <svg viewBox="0 0 16 16" aria-hidden="true"><g fill="none" stroke="#4fb9c5" stroke-width="1.5"><circle cx="8" cy="8" r="6.5"/><ellipse cx="8" cy="8" rx="3" ry="6.5"/><path d="M1.5 8h13"/></g></svg>
            www.brightlysettled.com
          </li>
          <li>
            <svg viewBox="0 0 16 16" aria-hidden="true"><rect x="1" y="3" width="14" height="10" fill="#4fb9c5"/><path d="M1 3l7 6 7-6" fill="none" stroke="#262626" stroke-width="1.3"/></svg>
            marisol@brightlysettled.com
          </li>
        </ul>
      </div>

      <div class="accent-rule"></div>
      <div class="base-strip"></div>
    </section>
  </main>
</body>
</html>
```